Online homewares store needs a web design

We need a web design for a new high-end online homewares store. We are starting small with only 5 major categories.

Rugs
Bathe
Dine
Decorative
Sleep

This is just for design. No coding needed.

Please make high-end, sophisticated and minimal.

I have included some pictures to give you an idea of the products. I would like to showcase some of the pictures on the web page.

The website will be using an e-commerce function.

I have included the logo studio nine harbors.

I like this website
http://mapleandquarrylane.example/

or

borvanest.example.au

Simple but effective - not too busy

Project Deadline Extended
Reason: I would like to extend my deadline to give designers more time to do quality work - as requested!! Thanks.

Target Market(s)

Females in the age bracket of 25-45

Males who are very house proud 25-45

Industry/Entity Type

Store

Requirements
Must have
• Upmarket

```html
<!DOCTYPE html>
<html lang="en">
<head>
<meta charset="utf-8">
<title>studio nine harbors — Home</title>
<link rel="stylesheet" href="https://fonts.googleapis.com/css2?family=Lato:wght@400;700&family=Questrial&display=swap">
<style>
  :root {
    --ink: #1c1c1c;
    --text: #3a3a3a;
    --accent: #e0306f;
    --rule: #e4e4e4;
    --faint: #d8d8d8;
    --icon: #707070;
    --bg: #ffffff;
  }
  * { box-sizing: border-box; margin: 0; padding: 0; }
  html, body { width: 1200px; height: 1031px; overflow: hidden; background: var(--bg); }
  body { position: relative; font-family: "Lato", sans-serif; color: var(--text); }

  .brand {
    position: absolute; left: 131px; top: 12px;
    font-family: "Questrial", sans-serif; font-size: 56px; letter-spacing: -1.5px;
    color: var(--ink); line-height: 1; white-space: nowrap;
  }

  .main-nav { position: absolute; top: 38px; left: 786px; height: 29px; }
  .main-nav a {
    font-size: 14px; text-decoration: none; color: var(--text);
    text-transform: uppercase; line-height: 29px; position: absolute; white-space: nowrap;
  }
  .main-nav .is-active {
    left: 0; width: 59px; text-align: center;
    background: var(--accent); color: #fff; font-weight: 700;
  }
  .main-nav .about { left: 110px; }
  .main-nav .shop { left: 240px; }

  .hero {
    position: absolute; left: 131px; top: 118px; width: 938px; height: 516px;
    background: radial-gradient(ellipse at 35% 30%, #d9a98d 0%, #c48a6c 22%, transparent 40%),
                linear-gradient(135deg, #5aa0c8 0%, #d84b6a 30%, #f0c04a 55%, #7fbf6a 75%, #8a5fb0 100%);
  }
  .hero-arrow { position: absolute; top: 359px; }
  .hero-arrow.prev { left: 141px; }
  .hero-arrow.next { left: 1043px; }

  .slider-dots { position: absolute; top: 652px; left: 566px; display: flex; gap: 7px; }
  .slider-dots span { width: 12px; height: 12px; border-radius: 50%; border: 1px solid #bdbdbd; }
  .slider-dots .is-current { border-color: var(--accent); border-width: 1.5px; }

  .categories { position: absolute; top: 692px; left: 131px; width: 938px; display: flex; gap: 33px; }
  .category { width: 291px; text-align: center; }
  .category-image { height: 216px; }
  .category-name { margin-top: 14px; font-family: "Questrial", sans-serif; font-size: 20px; color: var(--text); }
  .floor-art { background: linear-gradient(135deg, #e9e7e3 0%, #b9936a 35%, #9c7852 70%, #d8d2c8 100%); }
  .decorate { background: linear-gradient(135deg, #e4e0e4 0%, #c495c0 40%, #7d3d72 70%, #d65a98 100%); }
  .bathe { background: linear-gradient(135deg, #f2f1ef 0%, #c9433f 40%, #4d7fbf 65%, #ece9e4 100%); }

  .cat-arrow { position: absolute; top: 772px; }
  .cat-arrow.prev { left: 84px; }
  .cat-arrow.next { left: 1085px; }

  .site-footer {
    position: absolute; top: 980px; left: 0; width: 1200px; height: 51px;
    border-top: 1px solid var(--rule);
  }
  .copyright { position: absolute; left: 134px; top: 17px; font-size: 13.5px; color: var(--text); }
  .social { position: absolute; right: 132px; top: 19px; display: flex; gap: 9px; }
  .social-link { display: block; width: 14px; height: 14px; border-radius: 2px; background: var(--icon); }
</style>
</head>
<body>
  <header>
    <div class="brand">studio nine harbors</div>
    <nav class="main-nav">
      <a class="is-active" href="#">Home</a>
      <a class="about" href="#">About us</a>
      <a class="shop" href="#">Shop</a>
    </nav>
  </header>

  <main>
    <div class="hero" role="img" aria-label="Child's bare feet standing on a colourful felt ball rug"></div>
    <svg class="hero-arrow prev" width="16" height="34" viewBox="0 0 16 34"><path d="M15 1 L1 17 L15 33" fill="none" stroke="#fff" stroke-width="1.2" opacity=".8"/></svg>
    <svg class="hero-arrow next" width="16" height="34" viewBox="0 0 16 34"><path d="M1 1 L15 17 L1 33" fill="none" stroke="#fff" stroke-width="1.2"/></svg>

    <div class="slider-dots">
      <span class="is-current"></span><span></span><span></span><span></span>
    </div>

    <svg class="cat-arrow prev" width="30" height="56" viewBox="0 0 30 56"><path d="M28 1 L2 28 L28 55" fill="none" stroke="var(--faint)" stroke-width="1.2"/></svg>
    <section class="categories">
      <div class="category">
        <div class="category-image floor-art" role="img" aria-label="Round woven jute floor rug"></div>
        <p class="category-name">Floor Art</p>
      </div>
      <div class="category">
        <div class="category-image decorate" role="img" aria-label="Patterned cushions on a white chair"></div>
        <p class="category-name">Decorate</p>
      </div>
      <div class="category">
        <div class="category-image bathe" role="img" aria-label="Folded colourful woven towel with soap"></div>
        <p class="category-name">Bathe</p>
      </div>
    </section>
    <svg class="cat-arrow next" width="30" height="56" viewBox="0 0 30 56"><path d="M2 1 L28 28 L2 55" fill="none" stroke="var(--faint)" stroke-width="1.2"/></svg>
  </main>

  <footer class="site-footer">
    <p class="copyright">© 2014 Studionineharbors. All Rights Reserved.</p>
    <nav class="social" aria-label="Social links">
      <a class="social-link" href="#" aria-label="Social link 1"></a>
      <a class="social-link" href="#" aria-label="Social link 2"></a>
      <a class="social-link" href="#" aria-label="Social link 3"></a>
      <a class="social-link" href="#" aria-label="Social link 4"></a>
    </nav>
  </footer>
</body>
</html>
```